Maple Gable Business Card

Colors can be blue, grey and white as you see in the attached logo. Needs to have a spot for name, title, phone, email, address, and website. There also needs to be a spot for an agent's picture.

Contact Information for Business Card

See project description.

Colors

Designer to choose colors to be used in the design.

```html
<!DOCTYPE html>
<html lang="en">
<head>
<meta charset="utf-8">
<title>Maple Gable Business Card</title>
<link rel="stylesheet" href="https://fonts.googleapis.com/css2?family=Montserrat:wght@400;600;700&display=swap">
<style>
  :root {
    --brand-blue: #2f76b9;
    --brand-blue-light: #4a8ccb;
    --brand-grey: #3a3a3c;
    --photo-tone: #c9d6e4;
    --card-white: #ffffff;
    --stage: #e9e9ec;
  }
  * { margin: 0; padding: 0; box-sizing: border-box; }
  html, body {
    width: 1200px; height: 930px; overflow: hidden;
    background: var(--stage);
    font-family: "Montserrat", sans-serif;
  }
  .card {
    position: absolute;
    width: 620px; height: 360px;
    border-radius: 22px;
    overflow: hidden;
    box-shadow: 0 10px 28px rgba(0,0,0,0.18);
  }
  .card-back {
    left: 120px; top: 80px;
    background: linear-gradient(120deg, var(--brand-blue) 0%, var(--brand-blue-light) 35%, var(--brand-blue) 60%);
    display: flex; align-items: center; justify-content: center;
  }
  .brand-lockup {
    display: flex; align-items: center; gap: 14px;
    color: var(--card-white);
  }
  .brand-mark {
    width: 34px; height: 34px; background: var(--card-white);
  }
  .brand-name {
    font-weight: 700; font-size: 44px; letter-spacing: 1px; text-transform: uppercase;
  }
  .card-front {
    left: 460px; top: 480px;
    background: var(--card-white);
  }
  .front-shape { position: absolute; inset: 0; }
  .front-logo {
    position: absolute; right: 34px; top: 22px;
    display: flex; align-items: center; gap: 10px;
  }
  .front-logo .brand-mark { width: 22px; height: 22px; background: var(--brand-grey); }
  .front-logo .brand-name { font-size: 22px; color: var(--brand-blue); }
  .agent-photo {
    position: absolute; left: 36px; top: 40px;
    width: 84px; height: 84px; border-radius: 50%;
    background: linear-gradient(160deg, var(--photo-tone), #aebfd2);
  }
  .agent {
    position: absolute; left: 140px; top: 62px;
  }
  .agent-name {
    font-weight: 700; font-size: 24px; color: var(--brand-blue); letter-spacing: 0.5px; text-transform: uppercase;
  }
  .agent-title {
    font-size: 16px; color: var(--brand-grey); margin-top: 2px;
  }
  .contact-list {
    position: absolute; left: 34px; bottom: 20px;
    list-style: none; color: var(--card-white); font-size: 15px; line-height: 1.5;
  }
  .contact-list li { display: flex; align-items: center; gap: 10px; }
  .contact-list svg { width: 13px; height: 13px; flex: none; }
  .front-brand {
    position: absolute; right: 36px; top: 205px;
    color: var(--card-white);
    font-weight: 700; font-size: 30px; text-transform: uppercase; letter-spacing: 1px;
    display: flex; align-items: center; gap: 16px;
  }
  .front-brand .brand-mark { width: 44px; height: 44px; background: var(--card-white); }
</style>
</head>
<body>
  <section class="card card-back" aria-label="Card back">
    <div class="brand-lockup">
      <span class="brand-mark"></span>
      <span class="brand-name">Maple Gable</span>
    </div>
  </section>

  <section class="card card-front" aria-label="Card front">
    <svg class="front-shape" viewBox="0 0 620 360" preserveAspectRatio="none" aria-hidden="true">
      <defs>
        <linearGradient id="band" x1="0" y1="0" x2="1" y2="0.4">
          <stop offset="0" stop-color="#2f76b9"/>
          <stop offset="0.45" stop-color="#4a8ccb"/>
          <stop offset="1" stop-color="#2f76b9"/>
        </linearGradient>
      </defs>
      <polygon points="0,236 250,140 560,120 620,120 620,360 0,360" fill="url(#band)"/>
    </svg>

    <div class="front-logo">
      <span class="brand-mark"></span>
      <span class="brand-name">Maple Gable</span>
    </div>

    <div class="agent-photo" role="img" aria-label="Agent portrait photo"></div>

    <div class="agent">
      <p class="agent-name">Daniel Whitford</p>
      <p class="agent-title">Director</p>
    </div>

    <div class="front-brand">
      <span class="brand-mark"></span>
      <span>Maple Gable</span>
    </div>

    <ul class="contact-list">
      <li>
        <svg viewBox="0 0 24 24" fill="#fff"><path d="M6.6 10.8a15.1 15.1 0 0 0 6.6 6.6l2.2-2.2a1 1 0 0 1 1-.25 11.4 11.4 0 0 0 3.6.57 1 1 0 0 1 1 1V20a1 1 0 0 1-1 1A17 17 0 0 1 3 4a1 1 0 0 1 1-1h3.5a1 1 0 0 1 1 1c0 1.25.2 2.45.57 3.57a1 1 0 0 1-.25 1z"/></svg>
        (555) 014-2381
      </li>
      <li>
        <svg viewBox="0 0 24 24" fill="none" stroke="#fff" stroke-width="2.4"><rect x="3" y="5" width="18" height="14" rx="1"/><path d="M3 6l9 7 9-7"/></svg>
        info@maplegable.com
      </li>
      <li>
        <svg viewBox="0 0 24 24" fill="none" stroke="#fff" stroke-width="2"><circle cx="12" cy="12" r="9"/><path d="M3 12h18M12 3c3 3.5 3 14.5 0 18M12 3c-3 3.5-3 14.5 0 18"/></svg>
        www.maplegable.com
      </li>
      <li>
        <svg viewBox="0 0 24 24" fill="#fff"><path d="M12 2a7 7 0 0 0-7 7c0 5.2 7 13 7 13s7-7.8 7-13a7 7 0 0 0-7-7zm0 9.5a2.5 2.5 0 1 1 0-5 2.5 2.5 0 0 1 0 5z"/></svg>
        48 Orchard Lane, Milford
      </li>
    </ul>
  </section>
</body>
</html>
```